Webdesign for a business that converts shops into apps. UPDATE BRIEF

We want a creative/professional design for our new business Vorbo.

Vorbo is a service that can deliver instant apps for quillora shops. So every shop owner can have its own app for selling to there customers.

We are open for your interpretation of the design. We think it could be intersting doing an onepage design for this. But thats not set in stones offcourse.

We need several section:
top section
some facts abt the service and maybe our company
price table
some customer review
functionalitys of the app (in a nice way shown)
Section showing screens of a demo shop.
footer with ccdetails, socialmedia, newsletter

I have been playing abit myself with a theme, but no development/designer experience. And we really need a very professional and custom look.

Ps. we are an ecommerce company so if we find any good designer here, we will have enough work for you.

Some competitors in this field;

http://shrt.example/k7Tq2Zw
http://shrt.example/p3Nx9Ld

Here is a design we like
http://brelunoweb.example/

Hoping for some great concepts!

Kind Regards and good luck!

Some screenshots which can be used for app demo;

UPDATE BRIEF

We would like to add a section for features of the app.
We would like to show a zelphone screen and all the most important features of the app and when clicking every feature the screen would change or the feature intened would be high lighted in some way.

The features and any content and info abt that can be used from
https://www.tovexa.example/features.html/

We need an how it works section aswell in the design, also that can be used content from here
https://www.tovexa.example/how-it-works/

Tovexa is our partner, so there work way and features are same as ours. We just want it in a different 'look and feel/design)

Reason: Getting very few good design at the moment. Same designers seem to be responding whith 5 designs at a time of low quality.

Target Market(s)

quillora webshop

Industry/Entity Type

Business

Number of Pages Required

1 page

Font styles to use
Sans Serif

Colors
0355a3
3176b5
85acd3
85cae6
33a6d7
0392cd
f59195
33b8a4

Requirements
Must have
• a creative and custom look, not a copied theme vibe.
Nice to have
• it would be nice if the entire design has a nice flow goinf through the site. The customers experience should be on point.
Should not have
• boring static experience

```html
<!DOCTYPE html>
<html lang="nl">
<head>
<meta charset="utf-8">
<title>Vorbo – instant apps for Quillora shops</title>
<link href="https://fonts.googleapis.com/css2?family=Open+Sans:ital,wght@0,400;0,600;0,700;1,400&family=Quicksand:wght@700&family=Righteous&family=Nunito+Sans:wght@400;600;700&display=swap" rel="stylesheet">
<style>
:root{
  --blue-deep:#0355a3;
  --blue-mid:#3176b5;
  --blue-hero:#2f80d2;
  --cyan:#33a6d7;
  --cyan-title:#2a92d2;
  --teal:#33b8a4;
  --red:#ef5058;
  --navy:#1b4f8a;
  --ink:#222;
  --text:#555;
  --muted:#999;
  --line:#dedede;
  --band:#efefef;
  --star:#f5b800;
  --white:#fff;
}
*{box-sizing:border-box;margin:0;padding:0}
html,body{width:1200px;height:3352px;overflow:hidden}
body{position:relative;background:var(--white);font-family:"Open Sans",sans-serif;color:var(--text)}
.abs{position:absolute}
.section-title{position:absolute;left:0;width:1200px;text-align:center;font-family:"Righteous",sans-serif;font-size:31px;color:var(--ink);display:flex;justify-content:center;align-items:center;gap:26px}
.section-title::before,.section-title::after{content:"";width:90px;height:1px;background:#ccc}

/* hero */
.hero{position:absolute;left:0;top:0;width:1200px;height:577px;background:linear-gradient(120deg,#1f6cc4 0%,#3a8fe0 45%,#2a7bd0 100%)}
.logo{position:absolute;left:122px;top:18px;font-family:"Quicksand",sans-serif;font-weight:700;font-size:60px;color:var(--white);letter-spacing:1px}
.nav{position:absolute;top:50px;font-size:17px;color:var(--white);font-weight:600}
.hero-title{position:absolute;left:118px;top:252px;font-family:"Open Sans",sans-serif;font-weight:700;font-size:39px;line-height:45px;color:var(--white)}
.store-badge{position:absolute;top:369px;width:144px;height:36px;background:#111;border:1px solid #555;border-radius:6px}
.dots{position:absolute;left:566px;top:541px;display:flex;gap:4px}
.dots span{width:14px;height:14px;border-radius:50%;background:var(--white)}
.dots span:first-child{background:transparent;border:2px solid var(--white)}

/* company */
.company-title{top:616px;color:var(--cyan-title)}
.company-text{position:absolute;left:168px;top:672px;width:864px;text-align:center;font-size:15px;line-height:29px;color:var(--text)}
.fact-icon{position:absolute;top:831px}
.fact-title{position:absolute;font-size:24px;color:#333;font-weight:400}
.fact-text{position:absolute;font-size:12px;line-height:17px;color:var(--muted);width:230px}

/* price */
.price-title{top:1000px}
.card{position:absolute;top:1073px;width:313px;height:389px;border:1px solid var(--line);background:var(--white)}
.card svg{position:absolute;left:-1px;top:-1px}
.card .amount{position:absolute;left:0;top:36px;width:100%;text-align:center;font-family:"Nunito Sans",sans-serif;font-size:46px;font-weight:600;color:var(--white)}
.card .amount sup{font-size:24px;vertical-align:18px}
.card .plan{position:absolute;left:0;top:158px;width:100%;text-align:center;font-family:"Nunito Sans",sans-serif;font-size:26px;font-weight:700}
.card ul{position:absolute;left:28px;top:198px;width:255px;list-style:none}
.card li{height:30px;line-height:29px;text-align:center;font-size:13px;color:var(--text);border-bottom:1px solid #e8e8e8}
.card li:last-child{border-bottom:none}
.card .signup{position:absolute;left:95px;top:332px;width:123px;height:38px;border:1px solid #555;text-align:center;line-height:36px;font-size:13px;color:#333}

/* review */
.review-band{position:absolute;left:0;top:1547px;width:1200px;height:393px;background:var(--band)}
.review-title{top:1593px}
.quote{position:absolute;top:1663px;width:309px;height:156px;background:var(--white);border:1px solid #ddd;padding:36px 26px;font-style:italic;font-size:15px;line-height:26px;color:#777}
.quote::after{content:"";position:absolute;left:48px;bottom:-14px;width:24px;height:24px;background:var(--white);border-right:1px solid #ddd;border-bottom:1px solid #ddd;transform:rotate(45deg)}
.avatar{position:absolute;top:1840px;width:48px;height:48px;border-radius:50%;background:linear-gradient(#c9a58a,#6e5444)}
.author{position:absolute;top:1842px;font-size:14px;color:#333}
.stars{position:absolute;top:1862px;display:flex;gap:3px}

/* functionalities */
.phones{position:absolute;left:116px;top:2000px;width:371px;height:470px;border-radius:34px;background:linear-gradient(160deg,#f2f2f2,#cfd6de)}
.func-title{position:absolute;left:541px;top:2014px;font-family:"Righteous",sans-serif;font-size:32px;color:#1b5aa6}
.hex{position:absolute;left:543px}
.func-name{position:absolute;font-size:19px;color:#666}
.func-text{position:absolute;font-size:13px;line-height:19px;color:var(--text);width:440px}
.btn-outline{position:absolute;left:543px;top:2421px;width:139px;height:38px;border:2px solid var(--blue-deep);color:var(--blue-deep);font-size:13px;font-weight:600;text-align:center;line-height:34px}

/* demo */
.demo-band{position:absolute;left:0;top:2530px;width:1200px;height:394px;background:linear-gradient(135deg,#3170bb,#4a86c9)}
.demo-title{position:absolute;left:145px;top:2620px;font-family:"Righteous",sans-serif;font-size:38px;line-height:42px;color:var(--white)}
.demo-text{position:absolute;left:145px;top:2708px;width:590px;font-size:15px;line-height:29px;color:var(--white)}
.btn-white{position:absolute;left:147px;top:2805px;width:146px;height:38px;border:2px solid var(--white);color:var(--white);font-size:14px;font-weight:600;text-align:center;line-height:34px}
.demo-phone{position:absolute;left:771px;top:2604px;width:195px;height:320px;border-radius:28px 28px 0 0;background:linear-gradient(#f7f7f7,#dcdcdc)}

/* footer */
.foot-head{position:absolute;top:3014px;font-size:17px;font-weight:700;color:#333}
.foot-links{position:absolute;top:3056px;list-style:none;font-size:14px;line-height:27px;color:#777}
.contact-row{position:absolute;left:492px;display:flex;align-items:center;gap:10px;font-size:13px;line-height:19px;color:#666}
.pin{width:26px;height:26px;border-radius:50%;border:1px solid #3a6aa8;display:flex;align-items:center;justify-content:center;flex:none}
.news-input{position:absolute;left:776px;top:3051px;width:201px;height:40px;border:1px solid #ccc;font-size:12px;color:#999;line-height:38px;padding-left:14px}
.news-btn{position:absolute;left:977px;top:3051px;width:107px;height:40px;background:var(--red);color:var(--white);font-size:14px;font-weight:700;text-align:center;line-height:40px}
.social{position:absolute;top:3116px;width:18px;height:18px;border-radius:50%;background:var(--blue-mid)}
.card-pay{position:absolute;top:3158px;width:40px;height:22px;border-radius:3px;background:#d7dde6}
.foot-rule{position:absolute;left:116px;top:3268px;width:968px;height:1px;background:#e2e2e2}
.copyright{position:absolute;left:0;top:3285px;width:1200px;text-align:center;font-size:13px;color:#999}
</style>
</head>
<body>

<!-- hero -->
<header class="hero" role="img" aria-label="Photo of a woman using her phone, tinted blue"></header>
<div class="logo">vorbo</div>
<nav>
  <span class="nav" style="left:545px">About Us</span>
  <span class="nav" style="left:655px">Services</span>
  <span class="nav" style="left:755px">Price</span>
  <span class="nav" style="left:827px">Review</span>
  <span class="nav" style="left:921px">Demo</span>
  <span class="nav" style="left:1006px">Contact</span>
</nav>
<h1 class="hero-title">Direct meer omzet<br>meteen Quillora app</h1>
<div class="store-badge" style="left:118px"></div>
<div class="store-badge" style="left:277px"></div>
<div class="dots"><span></span><span></span><span></span><span></span></div>

<!-- company -->
<h2 class="section-title company-title">our company</h2>
<p class="company-text">Maecenas aliquet velit vel turpis Mauris neque metus malesuada nec ultricies sit amet porttitor mattis enim In massa libero interdum nec interdum vel blandit sed nulla In ullamcorper est eget tempor cursus neque mi consectetuer mi a ultricies massa est sed nisl Class aptent taciti sociosqu ad</p>

<svg class="fact-icon" style="left:150px" width="40" height="40" viewBox="0 0 40 40"><circle cx="20" cy="20" r="14" fill="none" stroke="#2a7ac8" stroke-width="7" stroke-dasharray="5 3.8"/><circle cx="20" cy="20" r="9" fill="#2a7ac8"/><circle cx="20" cy="20" r="4" fill="#fff"/></svg>
<div class="fact-title" style="left:203px;top:826px">Easy Setup</div>
<div class="fact-text" style="left:203px;top:866px">Maecenas aliquet velit vel turpis Mauris neque metus malesuada nec ultricies sit amet porttitor mattis enim</div>

<svg class="fact-icon" style="left:463px" width="44" height="40" viewBox="0 0 44 40"><path d="M4 16a14 11 0 1 1 8 10l-7 5 2-7a12 10 0 0 1-3-8z" fill="none" stroke="#2a9d8f" stroke-width="3"/><path d="M22 30a12 9 0 0 0 14-2l6 4-2-6" fill="none" stroke="#2a9d8f" stroke-width="3"/></svg>
<div class="fact-title" style="left:527px;top:820px">Dedicated Support</div>
<div class="fact-text" style="left:527px;top:860px">Maecenas aliquet velit vel turpis Mauris neque metus malesuada nec ultricies sit amet porttitor mattis enim</div>

<svg class="fact-icon" style="left:803px;top:822px" width="42" height="42" viewBox="0 0 42 42"><circle cx="21" cy="21" r="17" fill="none" stroke="#e03b43" stroke-width="4"/><path d="M21 11v11h8" fill="none" stroke="#e03b43" stroke-width="4"/></svg>
<div class="fact-title" style="left:858px;top:815px">On the Go</div>
<div class="fact-text" style="left:858px;top:853px">Maecenas aliquet velit vel turpis Mauris neque metus malesuada nec ultricies sit amet porttitor mattis enim</div>

<!-- price -->
<h2 class="section-title price-title">our price</h2>

<div class="card" style="left:116px">
  <svg width="313" height="150" viewBox="0 0 313 150"><path d="M0 0h313v112c-40 22-75 22-110 4s-70-20-105 0-70 20-98 4z" fill="var(--cyan)"/></svg>
  <div class="amount"><sup>$</sup>15.99</div>
  <div class="plan" style="color:var(--navy)">Basic</div>
  <ul><li>Praesent sit amet est In dictum</li><li>Dolor eu dictum</li><li>Porttitor enim felis viverra</li><li>Mi eget luctus massa</li></ul>
  <div class="signup">SIGN UP</div>
</div>
<div class="card" style="left:445px">
  <svg width="313" height="150" viewBox="0 0 313 150"><path d="M0 0h313v112c-40 22-75 22-110 4s-70-20-105 0-70 20-98 4z" fill="var(--teal)"/></svg>
  <div class="amount"><sup>$</sup>35.99</div>
  <div class="plan" style="color:var(--teal)">Advanced</div>
  <ul><li>Praesent sit amet est In dictum</li><li>Dolor eu dictum</li><li>Porttitor enim felis viverra</li><li>Mi eget luctus massa</li></ul>
  <div class="signup">SIGN UP</div>
</div>
<div class="card" style="left:773px">
  <svg width="313" height="150" viewBox="0 0 313 150"><path d="M0 0h313v112c-40 22-75 22-110 4s-70-20-105 0-70 20-98 4z" fill="var(--red)"/></svg>
  <div class="amount"><sup>$</sup>55.99</div>
  <div class="plan" style="color:var(--red)">Platinium</div>
  <ul><li>Praesent sit amet est In dictum</li><li>Dolor eu dictum</li><li>Porttitor enim felis viverra</li><li>Mi eget luctus massa</li></ul>
  <div class="signup">SIGN UP</div>
</div>

<!-- review -->
<section class="review-band"></section>
<h2 class="section-title review-title">customer review</h2>

<blockquote class="quote" style="left:116px">I love Nestra, I highly recommend it, Everyone Try it Now</blockquote>
<blockquote class="quote" style="left:447px">Keep It Up Guys Your Work Rules, Cheers</blockquote>
<blockquote class="quote" style="left:776px;padding-top:42px">Nestra is the best Statble, Fast App I have Ever Experienced</blockquote>

<div class="avatar" style="left:118px" role="img" aria-label="Customer portrait"></div>
<div class="author" style="left:179px">By Author Name</div>
<div class="stars" style="left:179px"><svg width="84" height="16" viewBox="0 0 84 16"><g fill="var(--star)"><path id="s" d="M8 0l2.4 5 5.6.7-4.1 3.8 1 5.5L8 12.3 3.1 15l1-5.5L0 5.7 5.6 5z"/><use href="#s" x="17"/><use href="#s" x="34"/><use href="#s" x="51"/></g></svg></div>

<div class="avatar" style="left:450px" role="img" aria-label="Customer portrait"></div>
<div class="author" style="left:510px">By Author Name</div>
<div class="stars" style="left:510px"><svg width="84" height="16" viewBox="0 0 84 16"><g fill="var(--star)"><use href="#s"/><use href="#s" x="17"/><use href="#s" x="34"/><use href="#s" x="51"/></g></svg></div>

<div class="avatar" style="left:781px;top:1843px" role="img" aria-label="Customer portrait"></div>
<div class="author" style="left:842px;top:1845px">By Author Name</div>
<div class="stars" style="left:842px;top:1866px"><svg width="84" height="16" viewBox="0 0 84 16"><g fill="var(--star)"><use href="#s"/><use href="#s" x="17"/><use href="#s" x="34"/><use href="#s" x="51"/></g></svg></div>

<!-- functionalities -->
<div class="phones" role="img" aria-label="Two zelphones showing the demo shop app checkout and category screens"></div>
<h2 class="func-title">Funotionalities of the app</h2>

<svg class="hex" style="top:2079px" width="83" height="98" viewBox="0 0 83 98"><path d="M41.5 2 81 25v48L41.5 96 2 73V25z" fill="#fff" stroke="#bbb" stroke-width="2"/><path d="M41.5 14 70 31v36L41.5 84 13 67V31z" fill="var(--blue-deep)"/><circle cx="41.5" cy="42" r="8" fill="#fff"/><path d="M27 66c0-10 7-14 14.5-14S56 56 56 66z" fill="#fff"/></svg>
<div class="func-name" style="left:637px;top:2088px">User Setting</div>
<div class="func-text" style="left:637px;top:2117px">interdum vel blandit sed nulla In ullamcorper est eget tempor cursus neque mi consectetuer mi a ultricies massa est sed</div>

<svg class="hex" style="top:2190px" width="83" height="98" viewBox="0 0 83 98"><path d="M41.5 2 81 25v48L41.5 96 2 73V25z" fill="#fff" stroke="#bbb" stroke-width="2"/><path d="M41.5 14 70 31v36L41.5 84 13 67V31z" fill="var(--blue-deep)"/><rect x="25" y="38" width="33" height="23" fill="#fff"/><path d="M25 38l16.5 13L58 38" fill="none" stroke="var(--blue-deep)" stroke-width="2.5"/></svg>
<div class="func-name" style="left:637px;top:2200px">Messsage &amp; Friend List</div>
<div class="func-text" style="left:637px;top:2229px">interdum vel blandit sed nulla In ullamcorper est eget tempor cursus neque mi consectetuer mi a ultricies massa est sed</div>

<svg class="hex" style="top:2298px" width="83" height="98" viewBox="0 0 83 98"><path d="M41.5 2 81 25v48L41.5 96 2 73V25z" fill="#fff" stroke="#bbb" stroke-width="2"/><path d="M41.5 14 70 31v36L41.5 84 13 67V31z" fill="var(--blue-deep)"/><rect x="26" y="35" width="31" height="28" fill="#fff"/><rect x="26" y="35" width="31" height="6" fill="#cfe0f2"/><g fill="var(--blue-deep)"><rect x="30" y="45" width="5" height="4"/><rect x="39" y="45" width="5" height="4"/><rect x="48" y="45" width="5" height="4"/><rect x="30" y="53" width="5" height="4"/><rect x="39" y="53" width="5" height="4"/><rect x="48" y="53" width="5" height="4"/></g></svg>
<div class="func-name" style="left:648px;top:2308px">Calender &amp; Live Chat</div>
<div class="func-text" style="left:648px;top:2337px">interdum vel blandit sed nulla In ullamcorper est eget tempor cursus neque mi consectetuer mi a ultricies massa est sed</div>

<div class="btn-outline">VIEW MORE</div>

<!-- demo -->
<section class="demo-band" role="img" aria-label="Blue band with faint line icons of shopping items"></section>
<h2 class="demo-title">sCreens of our<br>demo shop</h2>
<p class="demo-text">interdum vel blandit sed nulla In ullamcorper est eget tempor cursus neque mi a ultricies massa est sed nisl Class aptent taciti sociosqu ad litora torquent per conubia nostra per</p>
<div class="btn-white">READ MORE</div>
<div class="demo-phone" role="img" aria-label="Zelphone showing a product video screen of the demo shop"></div>

<!-- footer -->
<footer>
  <div class="foot-head" style="left:130px">COMPANY</div>
  <ul class="foot-links" style="left:130px"><li>Home</li><li>About</li><li>What we do</li><li>Team</li></ul>

  <div class="foot-head" style="left:306px">MARKETS</div>
  <ul class="foot-links" style="left:306px"><li>Training</li><li>Marketing</li><li>Createive Design</li><li>Media Buying</li></ul>

  <div class="foot-head" style="left:489px">CONTACT US</div>
  <div class="contact-row" style="top:3058px"><span class="pin"><svg width="10" height="14" viewBox="0 0 10 14"><path d="M5 0a5 5 0 0 1 5 5c0 4-5 9-5 9S0 9 0 5a5 5 0 0 1 5-5z" fill="#3a6aa8"/><circle cx="5" cy="5" r="2" fill="#fff"/></svg></span><span>418 Harbor Line Suite B12<br>Morrowfield, PA 19210</span></div>
  <div class="contact-row" style="top:3109px"><span class="pin"><svg width="12" height="12" viewBox="0 0 12 12"><path d="M2 0l2.5 3-1.2 1.5a7 7 0 0 0 4.2 4.2L9 7.5 12 10l-1.5 2C5 12 0 7 0 1.5z" fill="#3a6aa8"/></svg></span><span>+44 (0) 7000 481203</span></div>
  <div class="contact-row" style="top:3143px"><span class="pin"><svg width="12" height="9" viewBox="0 0 12 9"><rect width="12" height="9" fill="#3a6aa8"/><path d="M0 0l6 5 6-5" fill="none" stroke="#fff"/></svg></span><span>info@vorbo.example</span></div>

  <div class="foot-head" style="left:776px">NEWSLETTER SIGN UP</div>
  <div class="news-input">Email address</div>
  <div class="news-btn">SIGN UP</div>

  <span class="social" style="left:778px"></span>
  <span class="social" style="left:826px"></span>
  <span class="social" style="left:874px"></span>
  <span class="social" style="left:921px"></span>

  <span class="card-pay" style="left:776px"></span>
  <span class="card-pay" style="left:825px"></span>
  <span class="card-pay" style="left:874px"></span>
  <span class="card-pay" style="left:923px"></span>
  <span class="card-pay" style="left:972px"></span>

  <div class="foot-rule"></div>
  <div class="copyright">© 2016 Company Name &nbsp;All right reserved &nbsp;Term of Use</div>
</footer>

</body>
</html>
```